Landing Page / Waitlist

I would like a landing page for people to sign up for a waiting list. The text on the page should include (but is not limited to):
1) Main point: The accounting system you'll love
2) Secondary points:
a. Ruthlessly efficient
b. Quietly intelligent
c. Driven by AI
I've attached a file of our logo

The design should be simple, clean, and innovative - this is an ai company

```html
<!DOCTYPE html>
<html lang="en">
<head>
<meta charset="UTF-8">
<title>Ferrowick – Waitlist Landing Concepts</title>
<link rel="stylesheet" href="https://fonts.googleapis.com/css2?family=Poppins:wght@400;500;600;700;800&display=swap">
<style>
  :root {
    --page-bg: #c9c9c9;
    --brand-blue: #0a9bf5;
    --button-blue: #0896f8;
    --ink: #0b0b0b;
    --grey-text: #6a6a6a;
    --wordmark-grey: #6d6e71;
    --white: #ffffff;
    --field-border: #5f6368;
    --placeholder: #6b6b6b;
    --light-top: #ffffff;
    --light-mid: #e8f0f6;
    --light-wave: #8fb8d8;
    --light-bottom: #86cdf1;
    --night-top: #05082a;
    --night-mid: #060a2e;
    --ocean: #27588a;
    --ocean-deep: #1f4a78;
  }
  * { box-sizing: border-box; margin: 0; padding: 0; }
  html, body { width: 784px; height: 1200px; overflow: hidden; }
  body {
    background: var(--page-bg);
    font-family: "Poppins", sans-serif;
    position: relative;
  }
  .concept {
    position: absolute;
    left: 10px;
    width: 764px;
    height: 382px;
    overflow: hidden;
  }
  .concept--light { top: 13px; }
  .concept--night { top: 410px; }
  .concept--ocean { top: 802px; }

  .backdrop { position: absolute; inset: 0; }
  .concept--light .backdrop {
    background:
      radial-gradient(ellipse 40% 18% at 20% 68%, rgba(120,165,205,.55), transparent 70%),
      radial-gradient(ellipse 30% 16% at 62% 66%, rgba(120,165,205,.5), transparent 70%),
      radial-gradient(ellipse 22% 14% at 90% 70%, rgba(120,165,205,.45), transparent 70%),
      linear-gradient(180deg, var(--light-top) 0%, var(--light-top) 38%, var(--light-mid) 55%, var(--light-wave) 75%, var(--light-bottom) 100%);
  }
  .concept--night .backdrop {
    background:
      radial-gradient(ellipse 60% 30% at 50% 100%, rgba(138,42,74,.7), transparent 75%),
      radial-gradient(ellipse 70% 25% at 30% 95%, rgba(75,42,122,.8), transparent 75%),
      radial-gradient(ellipse 20% 45% at 48% 15%, rgba(80,60,140,.35), transparent 75%),
      linear-gradient(180deg, var(--night-top) 0%, var(--night-mid) 70%, #1a1445 100%);
  }
  .concept--ocean .backdrop {
    background:
      radial-gradient(ellipse 28% 40% at 72% 40%, rgba(95,159,214,.55), transparent 75%),
      radial-gradient(ellipse 30% 50% at 85% 55%, rgba(95,159,214,.35), transparent 75%),
      linear-gradient(90deg, var(--ocean) 0%, var(--ocean) 50%, var(--ocean-deep) 100%);
  }

  .content { position: absolute; inset: 0; }
  .content--centered { text-align: center; }

  .wordmark {
    position: absolute;
    font-weight: 600;
    font-size: 26px;
    line-height: 1;
    letter-spacing: -0.3px;
  }
  .content--centered .wordmark { left: 0; right: 0; }
  .concept--light .wordmark { top: 72px; color: var(--wordmark-grey); }
  .concept--night .wordmark { top: 77px; color: var(--white); }
  .concept--ocean .wordmark { top: 77px; left: 58px; color: var(--white); font-size: 27px; }

  .headline {
    position: absolute;
    font-weight: 700;
    line-height: 1.2;
  }
  .content--centered .headline { left: 0; right: 0; }
  .concept--light .headline { top: 116px; font-size: 26px; color: var(--ink); }
  .headline .accent { color: var(--brand-blue); }
  .concept--night .headline {
    top: 126px; font-size: 32px; font-weight: 800; color: var(--white); line-height: 1.15;
    text-shadow: 0 0 2px #7fd0ff, 0 0 6px rgba(90,190,255,.8);
  }
  .concept--ocean .headline { top: 131px; left: 58px; font-size: 28px; color: var(--white); line-height: 1.16; }

  .tagline {
    position: absolute;
    font-size: 10.5px;
    font-weight: 500;
  }
  .content--centered .tagline { left: 0; right: 0; }
  .tagline .dot { margin: 0 5px; font-size: 8px; vertical-align: 1px; }
  .concept--light .tagline { top: 160px; color: var(--grey-text); }
  .concept--night .tagline { top: 213px; color: var(--white); }
  .concept--ocean .tagline { top: 210px; left: 58px; color: var(--white); }

  .signup {
    position: absolute;
    display: flex;
    height: 28px;
  }
  .signup__field {
    flex: 1;
    background: var(--white);
    font-family: inherit;
    font-size: 8.5px;
    color: var(--placeholder);
    padding: 0 8px;
    border: none;
    outline: none;
    text-align: left;
  }
  .signup__field::placeholder { color: var(--placeholder); }
  .signup__button {
    background: var(--button-blue);
    color: var(--white);
    font-family: inherit;
    font-weight: 700;
    font-size: 9.5px;
    border: none;
  }
  .concept--light .signup { top: 197px; left: 182px; width: 389px; border: 1px solid var(--field-border); }
  .concept--light .signup__button { width: 117px; }
  .concept--night .signup { top: 250px; left: 184px; width: 391px; height: 29px; border: 1px solid #bfe6ff; }
  .concept--night .signup__field { padding-left: 10px; }
  .concept--night .signup__button { width: 128px; }
  .concept--ocean .signup { top: 253px; left: 57px; width: 328px; }
  .concept--ocean .signup__button { width: 128px; }

  .copyright {
    position: absolute;
    left: 0; right: 0;
    top: 356px;
    text-align: center;
    font-size: 8.5px;
    color: var(--ink);
  }
  .concept--night .copyright,
  .concept--ocean .copyright { color: var(--white); font-weight: 500; }
</style>
</head>
<body>

<section class="concept concept--light">
  <div class="backdrop" role="img" aria-label="Light blue digital wireframe landscape of rolling mesh hills"></div>
  <div class="content content--centered">
    <div class="wordmark">Ferrowick</div>
    <h1 class="headline">The <span class="accent">Accounting System</span> you'll love</h1>
    <p class="tagline">Ruthlessly efficient<span class="dot">●</span>Quietly intelligent<span class="dot">●</span>Driven by AI</p>
    <form class="signup">
      <input class="signup__field" type="email" placeholder="Enter Your Email Address">
      <button class="signup__button" type="button">Join the Waitlist</button>
    </form>
    <p class="copyright">Copyright © 2025. All rights reserved.</p>
  </div>
</section>

<section class="concept concept--night">
  <div class="backdrop" role="img" aria-label="Dark navy space with glowing purple and red light streaks converging toward the horizon"></div>
  <div class="content content--centered">
    <div class="wordmark">Ferrowick</div>
    <h1 class="headline">The Accounting System<br>you'll love</h1>
    <p class="tagline">Ruthlessly efficient<span class="dot">●</span>Quietly intelligent<span class="dot">●</span>Driven by AI</p>
    <form class="signup">
      <input class="signup__field" type="email" placeholder="Enter Your Email Address">
      <button class="signup__button" type="button">Join the Waitlist</button>
    </form>
    <p class="copyright">Copyright © 2025. All rights reserved.</p>
  </div>
</section>

<section class="concept concept--ocean">
  <div class="backdrop" role="img" aria-label="Blue technology scene with a hand on a laptop and a glowing AI network of connected icons"></div>
  <div class="content">
    <div class="wordmark">Ferrowick</div>
    <h1 class="headline">The Accounting System<br>you'll love</h1>
    <p class="tagline">Ruthlessly efficient<span class="dot">●</span>Quietly intelligent<span class="dot">●</span>Driven by AI</p>
    <form class="signup">
      <input class="signup__field" type="email" placeholder="Enter Your Email Address">
      <button class="signup__button" type="button">Join the Waitlist</button>
    </form>
    <p class="copyright">Copyright © 2025. All rights reserved.</p>
  </div>
</section>

</body>
</html>
```